Luxury Toilet Rental Business. Tallowby Hire.

Tallowby Hire (the logo is in the uploaded files)
We RENT and SELL Luxury Trailer toilets.
- Show location, number, pricing, pictures.
- We have two stall trailers for rent AND 3 stall trailers
- We sell them too
- We want our phone number shown
- We are a local company
- Slogan: Brighten your gathering with Tallowby Hire. The Velvet Privy
- We want a pricing portion
- We want the sizes shown
- We want the different rates/ prices shown
- We do 1 day rentals
- We do 1 week rentals
- We want the service area. We serve Los Angeles County, Orange County, Riverside County, San Bernardino County, and Palm Desert.
- Our location is in Santa Ana California

Target Market(s)

Event planners, wedding planners, venue planners, concerts, events, gatherings.

Industry/Entity Type

Luxury Toilet Rentals

Number of Pages Required

1 page

Font styles to use
Serif
Sans Serif

Colors
EE7325
F08F49
F5BC92
FAE3D3
FDF4ED

Requirements
Must have
• Location, pricing, pictures, available areas. Our slogan.
Nice to have
• I like the idea of having tabs that show price, a tab that shows our contact information, pictures, event ideas, and where we service (the areas we'll go to)

```html
<!DOCTYPE html>
<html lang="en">
<head>
<meta charset="utf-8">
<title>Tallowby Hire</title>
<link href="https://fonts.googleapis.com/css2?family=Roboto:wght@400;500;700&display=swap" rel="stylesheet">
<style>
:root{
  --orange:#ee7325;
  --orange-soft:#f08f49;
  --peach:#f5bc92;
  --ink:#222;
  --muted:#555;
  --white:#fff;
  --slate:#575759;
  --footer:#333;
}
*{box-sizing:border-box;margin:0;padding:0}
html,body{width:1200px;height:2550px;overflow:hidden}
body{font-family:'Roboto',sans-serif;color:var(--ink);background:var(--white);position:relative}
.abs{position:absolute}
a{color:inherit}
.btn{display:inline-flex;align-items:center;justify-content:center;background:var(--orange);color:var(--white);font-weight:500;text-decoration:none;letter-spacing:1px}
.btn-framed{outline:2px solid #fff;outline-offset:2px}
.icon-phone{width:14px;height:14px;margin-right:10px}

/* header */
.site-header{left:0;top:0;width:1200px;height:107px;background:var(--white)}
.brand{left:83px;top:34px;font-size:24px;font-weight:700;color:var(--orange);display:flex;align-items:center;gap:8px}
.brand-square{width:14px;height:14px;background:var(--orange)}
.nav{left:378px;top:45px;display:flex;gap:40px;font-size:13px}
.nav span{display:flex;align-items:center;gap:8px}
.header-call{left:909px;top:31px;width:206px;height:44px;font-size:13px;letter-spacing:0;outline:2px solid #555;outline-offset:3px}

/* hero */
.hero{left:0;top:107px;width:1200px;height:500px;background:linear-gradient(180deg,#6f6a60 0%,#5a5856 55%,#6b6b6b 100%)}
.hero-title{left:200px;top:246px;width:800px;text-align:center;color:var(--white);font-size:40px;font-weight:700;line-height:47px}
.hero-sub{left:260px;top:365px;width:680px;text-align:center;color:var(--white);font-size:19px;line-height:23px;font-weight:500}
.hero-rent{left:447px;top:437px;width:152px;height:46px;font-size:16px}
.hero-buy{left:613px;top:437px;width:140px;height:46px;border:2px solid #fff;color:#fff;font-size:16px;letter-spacing:1px;display:flex;align-items:center;justify-content:center}

/* trailers */
.section-title{font-size:33px;font-weight:700}
.trailers-title{left:0;top:690px;width:1200px;text-align:center}
.card{top:756px;width:459px;height:590px;background:#fff;box-shadow:0 2px 6px rgba(0,0,0,.18);overflow:hidden}
.card-photo{position:absolute;left:0;top:0;width:459px;height:333px}
.photo-arrow{position:absolute;top:273px;width:40px;height:40px;background:rgba(40,40,40,.75);display:flex;align-items:center;justify-content:center}
.card-body{position:absolute;left:20px;top:353px;width:420px}
.card-name{font-size:17px}
.card-size{font-size:12px;margin-top:10px}
.card-desc{font-size:12px;color:var(--muted);line-height:16px;margin-top:18px}
.price-row{display:flex;align-items:center;gap:8px;margin-top:26px}
.select{width:83px;height:25px;border:1px solid #999;font-size:11px;display:flex;align-items:center;justify-content:space-between;padding:0 10px}
.price{font-size:16px;font-weight:700}
.per{font-size:11px;font-weight:400;color:var(--muted)}
.info{width:9px;height:9px;border:1px solid #888;border-radius:50%;margin-top:-10px}
.action-row{display:flex;align-items:center;gap:14px;margin-top:14px}
.rent-now{width:128px;height:42px;font-size:13px}
.buy-link{font-size:12px;text-decoration:underline}
.pager{top:1393px;width:40px;height:40px;display:flex;align-items:center;justify-content:center}

/* service areas */
.areas{left:0;top:1536px;width:1200px;height:351px;background:var(--slate)}
.areas-map{left:0;top:1536px;width:560px;height:351px;background:linear-gradient(135deg,#4d4d4f,#616163)}
.areas-title{left:639px;top:1620px;color:#fff}
.areas-text{left:639px;top:1685px;width:485px;color:#fff;font-size:16px;font-weight:500;line-height:19px}
.areas-call{left:644px;top:1754px;width:206px;height:44px;font-size:13px;letter-spacing:0}
.areas-link{left:879px;top:1766px;color:#fff;font-size:16px;text-decoration:underline}

/* contact */
.contact{left:0;top:1887px;width:1200px;height:485px;background:linear-gradient(180deg,#4a4a4a,#2f2f30)}
.contact-title{left:83px;top:2040px;color:#fff}
.contact-text{left:83px;top:2104px;width:420px;color:#fff;font-size:16px;line-height:20px}
.contact-btn{left:86px;top:2172px;width:124px;height:44px;font-size:13px;letter-spacing:0}
.form{left:694px;top:1968px;width:423px}
.form-intro{display:flex;align-items:center;color:#fff;font-size:16px;gap:28px;margin-bottom:8px}
.form-select{width:128px;height:38px;background:#fff;color:#222;display:flex;align-items:center;justify-content:space-between;padding:0 14px}
.field{background:#fff;height:38px;margin-bottom:8px;color:#888;font-size:16px;padding:8px 10px}
.field.tall{height:82px}
.submit{width:423px;height:45px;font-size:16px;letter-spacing:1.5px}

/* footer */
.footer{left:0;top:2372px;width:1200px;height:178px;background:var(--footer);color:#fff}
.footer-brand{left:90px;top:2445px;font-size:22px;font-weight:700;color:var(--orange);display:flex;align-items:center;gap:8px}
.f-col{top:2428px;font-size:12px;line-height:16px;color:var(--white)}
.f-col h4{font-size:16px;font-weight:500;margin-bottom:12px;color:var(--white)}
.news-input{left:824px;top:2460px;width:193px;height:36px;border:1px solid #ccc;font-size:12px;padding:10px;color:#fff}
.news-btn{left:1024px;top:2460px;width:93px;height:36px;font-size:12px}
</style>
</head>
<body>

<header class="abs site-header">
  <div class="abs brand"><span class="brand-square"></span>Tallowby Hire</div>
  <nav class="abs nav">
    <span>Home</span>
    <span>Our Trailers <svg width="8" height="5" viewBox="0 0 8 5"><path d="M1 1l3 3 3-3" stroke="#333" fill="none"/></svg></span>
    <span>Services Area</span>
    <span>Contact Us</span>
  </nav>
  <a class="abs btn header-call"><svg class="icon-phone" viewBox="0 0 24 24"><path fill="#fff" d="M6.6 10.8a15 15 0 006.6 6.6l2.2-2.2c.3-.3.7-.4 1-.2 1.1.4 2.3.6 3.6.6.6 0 1 .4 1 1V20c0 .6-.4 1-1 1A17 17 0 013 4c0-.6.4-1 1-1h3.5c.6 0 1 .4 1 1 0 1.3.2 2.5.6 3.6.1.3 0 .7-.2 1z"/></svg>Call Us: 5550142837</a>
</header>

<section class="abs hero" role="img" aria-label="Photo of a luxury restroom trailer parked in a paved yard"></section>
<h1 class="abs hero-title">Brighten your gathering with Tallowby Hire. The Velvet Privy</h1>
<p class="abs hero-sub">Impress your guests with our lavish restroom options, adding a touch of refinement to your event.</p>
<a class="abs btn hero-rent">RENT</a>
<a class="abs hero-buy">BUY</a>

<h2 class="abs section-title trailers-title">Our Trailer</h2>

<article class="abs card" style="left:83px">
  <div class="card-photo" role="img" aria-label="Two-stall restroom trailer exterior" style="background:linear-gradient(180deg,#c9ccd0,#8e8f90)"></div>
  <div class="photo-arrow" style="left:20px"><svg width="14" height="20"><path d="M11 2L3 10l8 8" stroke="#fff" stroke-width="2.5" fill="none"/></svg></div>
  <div class="photo-arrow" style="left:399px"><svg width="14" height="20"><path d="M3 2l8 8-8 8" stroke="#fff" stroke-width="2.5" fill="none"/></svg></div>
  <div class="card-body">
    <div class="card-name">Trailer Name 1</div>
    <div class="card-size">Size: 7’ x 11’</div>
    <p class="card-desc">Lorem ipsum dolor sit amet consectetur. Nulla ac velit pharetra id pharetra at turpis libero. Amet sit dolor nisl massa tortor nulla magna enim nibh. Duis aliquam ultrices nisi pharetra massa augue cursus.</p>
    <div class="price-row"><span class="select">1 Week <svg width="8" height="5"><path d="M1 1l3 3 3-3" stroke="#333" fill="none"/></svg></span><span class="price">$123 - $456 <span class="per">/week</span></span><span class="info"></span></div>
    <div class="action-row"><a class="btn rent-now">RENT NOW</a><a class="buy-link">Want to buy this trailer?</a></div>
  </div>
</article>

<article class="abs card" style="left:568px">
  <div class="card-photo" role="img" aria-label="Restroom trailer interior with sink and toilet" style="background:linear-gradient(135deg,#eef0f2,#c9c6c2)"></div>
  <div class="photo-arrow" style="left:20px"><svg width="14" height="20"><path d="M11 2L3 10l8 8" stroke="#fff" stroke-width="2.5" fill="none"/></svg></div>
  <div class="photo-arrow" style="left:399px"><svg width="14" height="20"><path d="M3 2l8 8-8 8" stroke="#fff" stroke-width="2.5" fill="none"/></svg></div>
  <div class="card-body">
    <div class="card-name">Trailer Name 2</div>
    <div class="card-size">Size: 7’ x 11’</div>
    <p class="card-desc">Lorem ipsum dolor sit amet consectetur. Nulla ac velit pharetra id pharetra at turpis libero. Amet sit dolor nisl massa tortor nulla magna enim nibh. Duis aliquam ultrices nisi pharetra massa augue cursus.</p>
    <div class="price-row"><span class="select">1 Week <svg width="8" height="5"><path d="M1 1l3 3 3-3" stroke="#333" fill="none"/></svg></span><span class="price">$123 - $456 <span class="per">/week</span></span><span class="info"></span></div>
    <div class="action-row"><a class="btn rent-now">RENT NOW</a><a class="buy-link">Want to buy this trailer?</a></div>
  </div>
</article>

<article class="abs card" style="left:1053px">
  <div class="card-photo" role="img" aria-label="Three-stall restroom trailer exterior" style="background:linear-gradient(180deg,#c9ccd0,#8e8f90)"></div>
  <div class="photo-arrow" style="left:20px"><svg width="14" height="20"><path d="M11 2L3 10l8 8" stroke="#fff" stroke-width="2.5" fill="none"/></svg></div>
  <div class="card-body">
    <div class="card-name">Trailer Name 3</div>
    <div class="card-size">Size: 7’ x 11’</div>
    <p class="card-desc">Lorem ipsum dolor sit amet consectetur. Nulla ac velit pharetra id pharetra at turpis libero. Amet sit dolor nisl massa tortor nulla magna enim nibh. Duis aliquam ultrices nisi pharetra massa augue cursus.</p>
    <div class="price-row"><span class="select">1 Week <svg width="8" height="5"><path d="M1 1l3 3 3-3" stroke="#333" fill="none"/></svg></span><span class="price">$123 - $456 <span class="per">/week</span></span></div>
    <div class="action-row"><a class="btn rent-now">RENT NOW</a></div>
  </div>
</article>

<div class="abs pager" style="left:553px;background:#9a9a9a"><svg width="14" height="20"><path d="M11 2L3 10l8 8" stroke="#fff" stroke-width="2.5" fill="none"/></svg></div>
<div class="abs pager" style="left:606px;background:var(--peach)"><svg width="14" height="20"><path d="M3 2l8 8-8 8" stroke="#fff" stroke-width="2.5" fill="none"/></svg></div>

<section class="abs areas"></section>
<div class="abs areas-map" role="img" aria-label="Map of Southern California counties with service locations marked"></div>
<h2 class="abs section-title areas-title">Service Areas</h2>
<p class="abs areas-text">Lorem ipsum dolor sit amet consectetur. Morbi molestie fames mollis vel tellus cursus. Enim turpis volutpat ut nunc mauris.</p>
<a class="abs btn btn-framed areas-call"><svg class="icon-phone" viewBox="0 0 24 24"><path fill="#fff" d="M6.6 10.8a15 15 0 006.6 6.6l2.2-2.2c.3-.3.7-.4 1-.2 1.1.4 2.3.6 3.6.6.6 0 1 .4 1 1V20c0 .6-.4 1-1 1A17 17 0 013 4c0-.6.4-1 1-1h3.5c.6 0 1 .4 1 1 0 1.3.2 2.5.6 3.6.1.3 0 .7-.2 1z"/></svg>Call Us: 5550142837</a>
<a class="abs areas-link">Contact Us</a>

<section class="abs contact" role="img" aria-label="Dimmed photo of a restroom trailer with blue steps"></section>
<h2 class="abs section-title contact-title">Contact Us</h2>
<p class="abs contact-text">Do you have any questions, or want to discuss with us? Feel free to fill form below, or call us immediately</p>
<a class="abs btn btn-framed contact-btn">Contact Us</a>
<form class="abs form">
  <div class="form-intro"><span>I want to</span><span class="form-select">Rental <svg width="8" height="5"><path d="M1 1l3 3 3-3" stroke="#333" fill="none"/></svg></span><span>loo trailer.</span></div>
  <div class="field">Name</div>
  <div class="field">Email</div>
  <div class="field">Event</div>
  <div class="field tall">Message</div>
  <div class="btn submit">SUBMIT</div>
</form>

<footer class="abs footer"></footer>
<div class="abs footer-brand"><span class="brand-square"></span>Tallowby Hire</div>
<div class="abs f-col" style="left:345px"><h4>Location</h4>48 Harlow Lane<br>Santa Ana, CA 90001</div>
<div class="abs f-col" style="left:544px"><h4>Phone</h4>5550142837</div>
<div class="abs f-col" style="left:693px;line-height:22px"><h4 style="margin-bottom:6px">Trailers</h4>For Rent<br>For Sell</div>
<div class="abs f-col" style="left:824px"><h4>Newsletter</h4></div>
<div class="abs news-input">you@tallowbymail.com</div>
<div class="abs btn news-btn">SUBMIT</div>

</body>
</html>
```